Website Design for a holiday home letting busines

We require a redesign of our present website www.pinebrookstays.com. We want the website to stand out and look professional and clean to make holiday hunters want to book a caravan or lodge holiday with us. Our logo is red however we DO NOT want the website to be red. We want a natural colour scheme.

The final design should communicate that we are a professional company to book with.

On the home page we require;
Overview of company
Photo
Search box for holiday (check in)
Late Deals
Reviews
News

We would like the following pages designed; home page, available dates page, caravans page, content page.

The website should be responsive for smart phones. One website I do like is http://www.verdoliso.be/nl/

Target Market(s)

Families

Industry/Entity Type

Travel

Number of Pages Required

5+ page

Font styles to use
Serif

Requirements
Must have
• The project must be responsive for mobile phones and tablets.
• Ability to search for holiday home holidays
• We want a natural colour scheme.
Nice to have
• A style we like is http://www.verdoliso.be/nl/
Should not have
• Do not use red as a colour for the website. Our logo is red so this is the only time we want this used.

```html
<!DOCTYPE html>
<html lang="en">
<head>
<meta charset="utf-8">
<title>Pinebrook Stays – Holiday Lodges &amp; Caravans</title>
<link href="https://fonts.googleapis.com/css2?family=Open+Sans:wght@400;600;700&display=swap" rel="stylesheet">
<style>
:root{
  --orange:#f39a1e;
  --orange-dark:#e0850c;
  --blue:#1ea4e6;
  --blue-dark:#1677c2;
  --navy:#2a5d9a;
  --ink:#333;
  --muted:#777;
  --line:#e2e2e2;
  --paper:#fff;
  --grey-bg:#f3f3f3;
  --footer:#2c2c2c;
  --footer-dark:#1e1e1e;
}
*{box-sizing:border-box;margin:0;padding:0}
html,body{width:1200px;height:2812px;overflow:hidden}
body{font-family:"Open Sans",Arial,sans-serif;color:var(--ink);background:var(--paper);font-size:12px;line-height:1.5}
.wrap{width:960px;margin:0 auto;position:relative}

/* header */
.site-header{height:70px}
.site-header .wrap{display:flex;justify-content:space-between;align-items:center;height:70px}
.brand{font-size:24px;font-weight:700;color:var(--ink)}
.header-contact{display:flex;align-items:center;gap:18px}
.chat-btn{background:var(--blue);color:#fff;font-size:11px;font-weight:600;padding:6px 14px;border-radius:3px}
.phone-block{text-align:right}
.phone-block small{display:block;color:var(--orange);font-size:10px}
.phone{display:flex;align-items:center;gap:6px;font-size:20px;font-weight:700;color:var(--ink)}

/* nav */
.main-nav{background:var(--orange);height:32px}
.main-nav ul{list-style:none;display:flex;height:32px;align-items:center}
.main-nav li{color:#fff;font-size:11px;font-weight:600;padding:0 14px;height:32px;line-height:32px}
.main-nav li.active{background:var(--orange-dark)}

/* hero */
.hero{height:430px;position:relative;background:linear-gradient(180deg,#3b2a4a 0%,#b5542a 45%,#f2a23c 62%,#5a3a2a 80%,#1d1a1e 100%)}
.hero-text{position:absolute;left:120px;top:80px;width:420px;color:#fff}
.hero-text h1{font-size:38px;font-weight:700;line-height:1.1;text-shadow:0 1px 3px rgba(0,0,0,.4)}
.hero-text p{margin-top:8px;font-size:18px;font-weight:600;background:rgba(0,0,0,.35);padding:6px 10px;display:inline-block}
.btn-book{display:inline-block;margin-top:16px;background:#222;color:#fff;font-size:12px;font-weight:600;padding:8px 18px;border-radius:3px}
.circle{position:absolute;border-radius:50%;border:6px solid #fff;box-shadow:0 3px 10px rgba(0,0,0,.35)}
.circle.big{width:270px;height:270px;left:620px;top:40px;background:linear-gradient(135deg,#7fc6e8,#3a8fc2 60%,#e8d2b5)}
.circle.small-a{width:150px;height:150px;left:850px;top:30px;background:linear-gradient(135deg,#9fd8f0,#e9c9a2)}
.circle.small-b{width:150px;height:150px;left:870px;top:190px;background:linear-gradient(135deg,#5cb3dc,#c8e4f2)}
.hero-dots{position:absolute;left:120px;top:310px;display:flex;gap:6px}
.hero-dots span{width:9px;height:9px;border-radius:50%;background:rgba(255,255,255,.5)}
.hero-dots span:first-child{background:#fff}

/* feature row */
.feature-row{position:relative;height:120px}
.feature-row .wrap{display:flex;gap:14px;position:absolute;left:120px;top:-80px}
.feature-tile{width:250px;height:180px;background:#fff;box-shadow:0 2px 6px rgba(0,0,0,.2)}
.feature-tile .photo{height:140px}
.feature-tile .label{height:40px;line-height:40px;text-align:center;font-size:12px;font-weight:700;color:#333;background:#fff}
.feature-tile.orange .label{background:var(--orange);color:#fff}
.search-box{width:432px;height:210px;margin-top:-30px;background:var(--blue);color:#fff;padding:18px 20px 0;box-shadow:0 2px 6px rgba(0,0,0,.2);position:relative}
.search-box h3{font-size:15px;font-weight:600}
.search-box p{font-size:10px;opacity:.9}
.search-fields{display:flex;gap:8px;margin-top:14px}
.field{flex:1;height:28px;background:#fff;border-radius:2px;color:#888;font-size:10px;line-height:28px;padding:0 8px}
.field.btn{flex:.6;background:var(--orange);color:#fff;font-weight:600;text-align:center}
.search-box .label{position:absolute;left:0;right:0;bottom:0;height:40px;line-height:40px;text-align:center;background:var(--blue-dark);font-weight:700;font-size:12px}

/* overview */
.overview{background:var(--blue);color:#fff;height:340px;padding-top:40px}
.overview .wrap{display:flex;gap:40px}
.overview-text{width:520px}
.overview h2,.section-title{font-size:24px;font-weight:400;margin-bottom:14px}
.overview-text p{font-size:11px;margin-bottom:12px;opacity:.95}
.photo-grid{display:grid;grid-template-columns:repeat(3,1fr);gap:6px;width:400px}
.photo-grid div{height:80px;border:3px solid #fff}

/* news & reviews */
.news-reviews{height:330px;padding-top:40px}
.news-reviews .wrap{display:flex;gap:40px}
.col{flex:1}
.news-reviews .section-title{color:var(--blue);border-bottom:1px solid var(--line);padding-bottom:8px}
.post{padding:10px 0;border-bottom:1px solid var(--line)}
.post h4{font-size:12px;font-weight:600;color:var(--blue)}
.post p{font-size:11px;color:var(--muted)}
.post time{font-size:10px;color:#aaa}
.review{display:flex;gap:12px;padding:10px 0;border-bottom:1px solid var(--line)}
.review .thumb{width:80px;height:60px;flex:none}
.review h4{font-size:12px;font-weight:600;color:var(--orange)}
.review p{font-size:11px;color:var(--muted)}

/* deals */
.deals{height:510px;background:var(--grey-bg);padding-top:36px;border-top:1px solid var(--line)}
.deals .section-title{color:var(--ink)}
.card-row{display:flex;gap:20px;position:relative}
.card{width:225px;background:#fff;box-shadow:0 1px 4px rgba(0,0,0,.15)}
.card .photo{height:150px}
.card-body{padding:10px 12px}
.card h4{font-size:14px;color:var(--blue);font-weight:600}
.card .meta{font-size:10px;color:var(--muted)}
.spec{width:100%;border-collapse:collapse;margin-top:8px;font-size:10px}
.spec td{border:1px solid var(--line);padding:3px 5px;color:var(--muted)}
.card .cta{display:block;background:var(--blue);color:#fff;text-align:center;font-size:12px;font-weight:600;padding:9px 0}
.arrow{position:absolute;top:130px;width:24px;height:40px}
.arrow.left{left:-40px}
.arrow.right{right:-40px}

/* caravans */
.caravans{height:460px;background:var(--orange);padding-top:36px}
.caravans .section-title{color:#fff}

/* feeds */
.feeds{height:310px;padding-top:36px}
.feeds .wrap{display:flex;gap:24px}
.blog{flex:1.25}
.blog .section-title{color:var(--ink)}
.blog .post h4{color:var(--blue)}
.feed-box{width:230px;border:1px solid var(--line);align-self:flex-start}
.feed-box header{color:#fff;font-weight:600;font-size:13px;padding:10px 12px}
.feed-box.social header{background:var(--blue)}
.feed-box.community header{background:var(--navy)}
.feed-item{display:flex;gap:8px;padding:10px 12px;border-bottom:1px solid var(--line)}
.feed-item:last-child{border-bottom:0}
.feed-item .avatar{width:30px;height:30px;flex:none;background:#cfd8e0}
.feed-item p{font-size:10px;color:var(--muted)}
.feed-item strong{color:var(--blue);font-size:10px;display:block}

/* footer */
.site-footer{background:var(--footer);color:#bbb;height:162px;padding-top:26px}
.site-footer .wrap{display:flex;gap:30px}
.f-col{flex:1}
.f-col h5{color:#fff;font-size:11px;font-weight:700;margin-bottom:8px}
.f-col li{list-style:none;font-size:10px;line-height:1.8}
.socials{display:flex;gap:8px;margin-top:6px}
.socials span{width:16px;height:16px;border-radius:50%;background:#888}
.newsletter .input{height:26px;background:#fff;border-radius:2px;margin-bottom:8px}
.newsletter .go{display:inline-block;background:var(--orange);color:#fff;font-size:10px;font-weight:600;padding:5px 14px;border-radius:2px}
.footer-bar{background:var(--footer-dark);color:#888;font-size:10px;height:40px;line-height:40px}
</style>
</head>
<body>

<header class="site-header">
  <div class="wrap">
    <div class="brand">Pinebrook Stays</div>
    <div class="header-contact">
      <span class="chat-btn">Live Chat</span>
      <div class="phone-block">
        <small>Call us today for help</small>
        <div class="phone">
          <svg width="18" height="18" viewBox="0 0 24 24"><path fill="#1ea4e6" d="M6.6 10.8a15 15 0 006.6 6.6l2.2-2.2c.3-.3.7-.4 1-.2 1.1.4 2.3.6 3.6.6.6 0 1 .4 1 1V20c0 .6-.4 1-1 1A17 17 0 013 4c0-.6.4-1 1-1h3.5c.6 0 1 .4 1 1 0 1.3.2 2.5.6 3.6.1.3 0 .7-.2 1z"/></svg>
          07700 900 461
        </div>
      </div>
    </div>
  </div>
</header>

<nav class="main-nav">
  <ul class="wrap">
    <li class="active">HOME</li><li>NEWS</li><li>CARAVANS &amp; LODGES</li><li>2013 HOLIDAYS</li><li>2014 HOLIDAYS</li><li>LOCAL ATTRACTIONS</li><li>CONTACT US</li>
  </ul>
</nav>

<section class="hero" role="img" aria-label="Sunset over a lakeside holiday park with palm trees">
  <div class="hero-text">
    <h1>Private Holiday Rentals</h1>
    <p>Overlooking a lake at the<br>Alderbeck Hollow Holiday Park</p><br>
    <span class="btn-book">Book Now</span>
  </div>
  <div class="hero-dots"><span></span><span></span><span></span><span></span></div>
  <div class="circle big" role="img" aria-label="Family relaxing by the holiday park pool"></div>
  <div class="circle small-a" role="img" aria-label="Couple enjoying a sunny break"></div>
  <div class="circle small-b" role="img" aria-label="Outdoor swimming pool"></div>
</section>

<section class="feature-row">
  <div class="wrap">
    <div class="feature-tile">
      <div class="photo" role="img" aria-label="Lodge by the water" style="background:linear-gradient(135deg,#6fb7de,#2f7fb0 55%,#c9b58e)"></div>
      <div class="label">WHY OUR LODGES</div>
    </div>
    <div class="feature-tile orange">
      <div class="photo" role="img" aria-label="Resort pool surrounded by palms" style="background:linear-gradient(135deg,#8ed0ef,#3aa3d6 55%,#7ca35a)"></div>
      <div class="label">LOCAL ATTRACTIONS</div>
    </div>
    <div class="search-box">
      <h3>Book Your Holiday with us</h3>
      <p>Choose your dates and find an available lodge</p>
      <div class="search-fields">
        <div class="field">Check in</div>
        <div class="field">Nights</div>
        <div class="field btn">Search</div>
      </div>
      <div class="label">SEARCH BOX FOR HOLIDAY</div>
    </div>
  </div>
</section>

<section class="overview">
  <div class="wrap">
    <div class="overview-text">
      <h2>Overview of Company</h2>
      <p>We are a family run business offering quality caravans and lodges to let on a peaceful lakeside park. Every holiday home is cleaned, checked and fully equipped before you arrive so you can relax from day one.</p>
      <p>Our homes suit couples, families and groups of friends. Each one has modern kitchens, comfortable lounges and private decking with views across the water and the open countryside around the park.</p>
      <p>Booking direct with us means friendly help, fair prices and no hidden fees. Browse our late deals below or search for your dates to check what is free.</p>
    </div>
    <div>
      <h2>Our Photos</h2>
      <div class="photo-grid">
        <div role="img" aria-label="Lodge exterior" style="background:linear-gradient(135deg,#d9c7a6,#8b6f4e)"></div>
        <div role="img" aria-label="Holiday park pool" style="background:linear-gradient(135deg,#9fd6f2,#3e93c6)"></div>
        <div role="img" aria-label="Lounge interior" style="background:linear-gradient(135deg,#efe4d2,#b79c7a)"></div>
        <div role="img" aria-label="Lake view" style="background:linear-gradient(135deg,#a7d2ea,#5a8f6a)"></div>
        <div role="img" aria-label="Bedroom interior" style="background:linear-gradient(135deg,#f1e8db,#c7a98a)"></div>
        <div role="img" aria-label="Children playing outdoors" style="background:linear-gradient(135deg,#bfe2b0,#6aa45a)"></div>
      </div>
    </div>
  </div>
</section>

<section class="news-reviews">
  <div class="wrap">
    <div class="col">
      <h2 class="section-title">Recent News</h2>
      <article class="post">
        <h4>New lakeside lodges ready for the summer season</h4>
        <p>Three new lodges open this spring with hot tubs and private decks facing the lake.</p>
        <time>20 Aug 2013</time>
      </article>
      <article class="post">
        <h4>Refreshed pool and play area</h4>
        <p>The park pool has reopened after a full refit, with a new splash zone for little ones.</p>
        <time>12 Aug 2013</time>
      </article>
    </div>
    <div class="col">
      <h2 class="section-title">Latest Reviews</h2>
      <div class="review">
        <div class="thumb" role="img" aria-label="Caravan lounge" style="background:linear-gradient(135deg,#efe2cf,#b59672)"></div>
        <div><h4>A perfect family week</h4><p>Spotless caravan, great views and a warm welcome. The kids loved the pool and we will return next year.</p></div>
      </div>
      <div class="review">
        <div class="thumb" role="img" aria-label="Lodge kitchen" style="background:linear-gradient(135deg,#e6ddd0,#9a8a74)"></div>
        <div><h4>Relaxing and well looked after</h4><p>Everything we needed was there on arrival. Quiet spot, easy booking and very helpful owners.</p></div>
      </div>
    </div>
  </div>
</section>

<section class="deals">
  <div class="wrap">
    <h2 class="section-title">Late Deals</h2>
    <div class="card-row">
      <svg class="arrow left" viewBox="0 0 24 40"><path d="M20 2L4 20l16 18" fill="none" stroke="#aaa" stroke-width="3"/></svg>
      <svg class="arrow right" viewBox="0 0 24 40"><path d="M4 2l16 18L4 38" fill="none" stroke="#aaa" stroke-width="3"/></svg>
      <div class="card">
        <div class="photo" role="img" aria-label="Caravan lounge" style="background:linear-gradient(135deg,#efe3d0,#a88a66)"></div>
        <div class="card-body"><h4>The Florida</h4><p class="meta">Friday 20 September 2013 (3 nights)</p>
          <table class="spec"><tr><td>Caravan type</td><td>Deluxe</td></tr><tr><td>Sleeps</td><td>6</td></tr><tr><td>Bedrooms</td><td>3</td></tr></table></div>
        <span class="cta">Book Now for £ 275.00</span>
      </div>
      <div class="card">
        <div class="photo" role="img" aria-label="Caravan dining area" style="background:linear-gradient(135deg,#e9dccb,#9d7f5e)"></div>
        <div class="card-body"><h4>The Florida</h4><p class="meta">Friday 20 September 2013 (3 nights)</p>
          <table class="spec"><tr><td>Caravan type</td><td>Deluxe</td></tr><tr><td>Sleeps</td><td>6</td></tr><tr><td>Bedrooms</td><td>3</td></tr></table></div>
        <span class="cta">Book Now for £ 275.00</span>
      </div>
      <div class="card">
        <div class="photo" role="img" aria-label="Caravan kitchen" style="background:linear-gradient(135deg,#f0e8dc,#b39c80)"></div>
        <div class="card-body"><h4>The Florida</h4><p class="meta">Friday 20 September 2013 (3 nights)</p>
          <table class="spec"><tr><td>Caravan type</td><td>Deluxe</td></tr><tr><td>Sleeps</td><td>6</td></tr><tr><td>Bedrooms</td><td>3</td></tr></table></div>
        <span class="cta">Book Now for £ 275.00</span>
      </div>
      <div class="card">
        <div class="photo" role="img" aria-label="Caravan bedroom" style="background:linear-gradient(135deg,#eadfce,#a48565)"></div>
        <div class="card-body"><h4>The Florida</h4><p class="meta">Friday 20 September 2013 (3 nights)</p>
          <table class="spec"><tr><td>Caravan type</td><td>Deluxe</td></tr><tr><td>Sleeps</td><td>6</td></tr><tr><td>Bedrooms</td><td>3</td></tr></table></div>
        <span class="cta">Book Now for £ 275.00</span>
      </div>
    </div>
  </div>
</section>

<section class="caravans">
  <div class="wrap">
    <h2 class="section-title">Our Caravans and Lodges</h2>
    <div class="card-row">
      <svg class="arrow left" viewBox="0 0 24 40"><path d="M20 2L4 20l16 18" fill="none" stroke="#fff" stroke-width="3"/></svg>
      <svg class="arrow right" viewBox="0 0 24 40"><path d="M4 2l16 18L4 38" fill="none" stroke="#fff" stroke-width="3"/></svg>
      <div class="card">
        <div class="photo" role="img" aria-label="Lodge living room" style="background:linear-gradient(135deg,#efe3d0,#a88a66)"></div>
        <div class="card-body"><h4>The Florida</h4><p class="meta">Lakeside plot with private decking</p>
          <table class="spec"><tr><td>Caravan type</td><td>Deluxe</td></tr><tr><td>Sleeps</td><td>6</td></tr><tr><td>Bedrooms</td><td>3</td></tr></table></div>
        <span class="cta">More Details</span>
      </div>
      <div class="card">
        <div class="photo" role="img" aria-label="Caravan exterior" style="background:linear-gradient(135deg,#dfe8ee,#8ea5b5)"></div>
        <div class="card-body"><h4>The Florida</h4><p class="meta">Lakeside plot with private decking</p>
          <table class="spec"><tr><td>Caravan type</td><td>Deluxe</td></tr><tr><td>Sleeps</td><td>6</td></tr><tr><td>Bedrooms</td><td>3</td></tr></table></div>
        <span class="cta">More Details</span>
      </div>
      <div class="card">
        <div class="photo" role="img" aria-label="Lodge lounge with sofas" style="background:linear-gradient(135deg,#f0e8dc,#b39c80)"></div>
        <div class="card-body"><h4>The Florida</h4><p class="meta">Lakeside plot with private decking</p>
          <table class="spec"><tr><td>Caravan type</td><td>Deluxe</td></tr><tr><td>Sleeps</td><td>6</td></tr><tr><td>Bedrooms</td><td>3</td></tr></table></div>
        <span class="cta">More Details</span>
      </div>
      <div class="card">
        <div class="photo" role="img" aria-label="Caravan dining area" style="background:linear-gradient(135deg,#eadfce,#a48565)"></div>
        <div class="card-body"><h4>The Florida</h4><p class="meta">Lakeside plot with private decking</p>
          <table class="spec"><tr><td>Caravan type</td><td>Deluxe</td></tr><tr><td>Sleeps</td><td>6</td></tr><tr><td>Bedrooms</td><td>3</td></tr></table></div>
        <span class="cta">More Details</span>
      </div>
    </div>
  </div>
</section>

<section class="feeds">
  <div class="wrap">
    <div class="blog">
      <h2 class="section-title">Blog Feed</h2>
      <article class="post"><h4>Planning your first lodge break</h4><p>Handy tips on packing, arrival times and what is included in every holiday home.</p><time>Posted 3 days ago</time></article>
      <article class="post"><h4>Best walks around the lake</h4><p>Our favourite family trails, from short strolls to longer routes with great views.</p><time>Posted 6 days ago</time></article>
    </div>
    <div class="feed-box social">
      <header>Social Feed</header>
      <div class="feed-item"><span class="avatar"></span><p><strong>Pinebrook Stays</strong>Late deal just added for this weekend, three nights from £275.</p></div>
      <div class="feed-item"><span class="avatar"></span><p><strong>Pinebrook Stays</strong>The pool is open again after its refit. Come and try the splash zone.</p></div>
    </div>
    <div class="feed-box community">
      <header>Community Feed</header>
      <div class="feed-item"><span class="avatar"></span><p><strong>Pinebrook Stays</strong>Thank you to all our guests for the lovely reviews this month.</p></div>
      <div class="feed-item"><span class="avatar"></span><p><strong>Pinebrook Stays</strong>New photos of our lakeside lodges are now on the website.</p></div>
    </div>
  </div>
</section>

<footer>
  <div class="site-footer">
    <div class="wrap">
      <div class="f-col"><h5>QUICK LINKS</h5><ul><li>Home</li><li>About Us</li><li>Caravans &amp; Lodges</li><li>2014 Holidays</li></ul></div>
      <div class="f-col"><h5>RESOURCES</h5><ul><li>Our Reviews</li><li>Booking</li><li>Reviews</li><li>Blog &amp; News</li></ul></div>
      <div class="f-col"><h5>CONTACT INFO</h5><ul><li>T: 07700 900 461</li><li>www.pinebrookstays.com</li><li>hello@pinebrookstays.com</li></ul>
        <div class="socials"><span></span><span></span><span></span><span></span></div></div>
      <div class="f-col newsletter"><h5>NEWSLETTER SUBSCRIBE</h5><div class="input"></div><span class="go">Subscribe</span></div>
    </div>
  </div>
  <div class="footer-bar"><div class="wrap">© 2013 Pinebrook Stays. All rights reserved. | Privacy Policy</div></div>
</footer>

</body>
</html>
```